VFX Company Business Card Design Project

The Kestrel Works is a decentralized Visual Effects Studio servicing the television and feature film industries.
Project Brief:
Take our logo that was previously designed on Pencil Harbor and make a double sided business card.
Requirements:
- Card MUST be double sided.
- Front of card MUST have the yellow part of our logo against the dark grey background.
- Back of card is completely up to the designer.
- Back of card must include the complete company logo.
Please follow these File Preparation guidelines:
http://printnook.ca/infopage?file=filetype_en&s=PrintNook_new&lang=en
Business

```html
<!DOCTYPE html>
<html lang="en">
<head>
<meta charset="utf-8">
<title>The Kestrel Works – Business Cards</title>
<link rel="stylesheet" href="https://fonts.googleapis.com/css2?family=Montserrat:wght@600&family=Questrial&family=Bitter:wght@400;700&display=swap">
<style>
  :root {
    --stage: #b8a48e;
    --charcoal: #262626;
    --slate: #5f6b6e;
    --paper: #eaefe3;
    --sun: #ffc629;
    --ink: #1d1d1d;
    --white: #ffffff;
    --rule: #8c9190;
  }
  * { box-sizing: border-box; margin: 0; padding: 0; }
  html, body { width: 1200px; height: 734px; overflow: hidden; }
  body {
    position: relative;
    background: var(--stage);
    font-family: "Questrial", sans-serif;
  }
  .card {
    position: absolute;
    width: 523px;
    height: 299px;
    border-radius: 26px;
    overflow: hidden;
  }
  .card--front  { left: 67px;  top: 43px;  background: var(--charcoal); }
  .card--details{ left: 628px; top: 47px;  background: var(--charcoal); }
  .card--light  { left: 64px;  top: 384px; background: var(--paper); }
  .card--slate  { left: 622px; top: 388px; background: var(--slate); }

  .wordmark {
    font-family: "Montserrat", sans-serif;
    font-weight: 600;
    letter-spacing: -0.5px;
    line-height: 1;
    white-space: nowrap;
  }
  .tagline {
    font-family: "Questrial", sans-serif;
    letter-spacing: 7px;
    line-height: 1;
    white-space: nowrap;
  }

  /* Front */
  .front-mark {
    position: absolute; inset: 0;
    display: flex; align-items: center; justify-content: center; gap: 18px;
  }
  .front-mark .dot { width: 34px; height: 34px; border-radius: 50%; background: var(--sun); }
  .front-mark .wordmark { color: var(--sun); font-size: 44px; }

  /* Details side */
  .details-head { position: absolute; left: 0; right: 0; top: 36px; text-align: center; }
  .details-head .wordmark { color: var(--white); font-size: 40px; }
  .details-head .tagline { color: var(--white); font-size: 19px; margin-top: 12px; letter-spacing: 8px; }
  .details-band {
    position: absolute; left: 0; right: 0; top: 154px; height: 107px;
    background: var(--paper);
    border-top: 2px solid var(--rule);
    border-bottom: 2px solid var(--rule);
    font-family: "Bitter", serif; font-size: 13.5px; color: var(--ink);
  }
  .address { position: absolute; right: 311px; top: 34px; text-align: right; line-height: 21px; }
  .divider { position: absolute; left: 228px; top: 20px; width: 1px; height: 54px; background: var(--rule); }
  .contacts { position: absolute; left: 244px; top: 14px; list-style: none; line-height: 19.5px; }
  .contacts li { display: flex; align-items: center; gap: 6px; }
  .contacts svg { width: 10px; height: 10px; fill: var(--ink); }
  .signature {
    position: absolute; left: 0; right: 0; bottom: 10px; text-align: center;
    font-family: "Bitter", serif; color: var(--white);
  }
  .signature .name { font-weight: 700; font-size: 17px; }
  .signature .title { font-size: 13px; }

  /* Light back */
  .light-mark { position: absolute; left: 0; right: 0; top: 116px; text-align: center; }
  .light-mark .wordmark { color: var(--ink); font-size: 38px; }
  .light-mark .tagline { color: var(--ink); font-size: 15px; margin-top: 9px; }
  .web { position: absolute; left: 0; right: 0; bottom: 24px; text-align: center; font-size: 16px; letter-spacing: 3px; }
  .card--light .web { color: var(--ink); }

  /* Slate back */
  .slate-mark { position: absolute; left: 0; right: 0; top: 100px; text-align: center; }
  .slate-mark .wordmark { color: var(--white); font-size: 50px; }
  .slate-mark .tagline { color: var(--white); font-size: 21px; margin-top: 12px; letter-spacing: 9px; }
  .card--slate .web { color: var(--white); bottom: 20px; }
</style>
</head>
<body>

<section class="card card--front" aria-label="Card front">
  <div class="front-mark">
    <span class="dot"></span>
    <span class="wordmark">The Kestrel Works</span>
  </div>
</section>

<section class="card card--details" aria-label="Card back with contact details">
  <header class="details-head">
    <div class="wordmark">The Kestrel Works</div>
    <div class="tagline">VIRTUAL STUDIO</div>
  </header>
  <div class="details-band">
    <address class="address" style="font-style:normal">00, Complex name<br>City, State 0042</address>
    <span class="divider"></span>
    <ul class="contacts">
      <li><svg viewBox="0 0 10 10"><path d="M2 0h2l1 3-1.5 1a5 5 0 0 0 2.5 2.5L7 5l3 1v2c0 1-1 2-2 2A8 8 0 0 1 0 2c0-1 1-2 2-2z"/></svg>0123 987650</li>
      <li><svg viewBox="0 0 10 10"><rect x="2.5" y="0" width="5" height="10" rx="1"/></svg>0123 987650</li>
      <li><svg viewBox="0 0 10 10"><path d="M0 2h10v6H0z M0 2l5 3 5-3" /></svg>info@kestrelworks.com</li>
      <li><svg viewBox="0 0 10 10"><circle cx="5" cy="5" r="5"/></svg>www.kestrelworks.com</li>
    </ul>
  </div>
  <p class="signature"><span class="name">Your Name,</span> <span class="title">Title</span></p>
</section>

<section class="card card--light" aria-label="Card back, light version">
  <div class="light-mark">
    <div class="wordmark">The Kestrel Works</div>
    <div class="tagline">VIRTUAL STUDIO</div>
  </div>
  <p class="web">www.kestrelworks.com</p>
</section>

<section class="card card--slate" aria-label="Card back, slate version">
  <div class="slate-mark">
    <div class="wordmark">The Kestrel Works</div>
    <div class="tagline">VIRTUAL STUDIO</div>
  </div>
  <p class="web">www.kestrelworks.com</p>
</section>

</body>
</html>
```